Nitrogen generation business website

Project Overview:
This project aims to create a sleek, user-friendly, and responsive WordPress template for Flo7K3, a provider of Nitrogen generation solutions. The site will serve as a primary touchpoint for customers and businesses looking to enquire about or purchase Flo7K3 products and services. The website should clearly communicate the benefits of working with Flo7K3 as a distributor, focusing on ease of access, expert consultation, and fast, reliable service.
Target Audience:
• Industrial companies seeking Nitrogen solutions.
• Engineers, facility managers, and purchasing teams in need of high-quality Nitrogen systems.
• Partners or businesses seeking to collaborate or purchase through a distributor.
Key Objectives:
1. Establish Flo7K3’s Brand Identity: Use the bold, energetic logo and branding of Flo7K3 (as seen in the uploaded logo) throughout the design. Ensure the brand’s personality shines, with a focus on modernity, reliability, and innovation.
2. Showcase Products and Solutions: Display detailed product categories and descriptions, emphasising the solutions Flo7K3 offers.
3. Lead Generation: Incorporate contact forms, quote requests, and easy-to-find CTAs to convert visitors into leads.
4. User-Centric Design: The design must be intuitive and user-friendly, providing a smooth experience across desktop and mobile devices.
Design Requirements:
1. Home Page:
• Hero Banner: A dynamic, visually engaging hero banner featuring air and gas purification systems, paired with strong CTAs like “Request a Quote” or “Contact Us for Solutions.” The banner should align with the vibrant red and yellow tones in the Flo7K3 logo.
• Key Product Categories: Introduce the main product categories with icons or images linked to individual product pages.
• Flo7K3 Expertise Section: A section emphasising the company’s role as a trusted distributor, backed by experience and a strong partnership network.
• Why Choose Flo7K3: Highlight 3-4 major benefits, such as “Quick Delivery,” “Expert Consultation,” and “Innovative Technology.”
• Client Testimonials/Partners: Space for customer feedback, testimonials, or logos of partner companies to build trust.
• Newsletter or Enquiry Form: Place a compact form for capturing visitor details for quotes, enquiries, or subscriptions.
2. Product Pages:
• Category Pages: Create well-structured product category pages (e.g., Air Filtration Systems, Nitrogen Generators) similar to industry-standard designs. Each category page should feature professional imagery, short product descriptions, and links to detail pages.
• Product Detail Pages: Each product page will contain:
• High-quality images of the product.
• Detailed specifications, technical descriptions, and features.
• Options to download datasheets or brochures (PDF format).
• Clear CTAs to request a quote or contact sales.
• Product Comparison Tool (Optional): Allow users to compare multiple products, emphasising key features and specifications.
3. About Flo7K3 Page:
• Provide an overview of Flo7K3’s history, mission, and the value it provides as a leading distributor.
• Highlight industry expertise, the partnership network, and any accolades or certifications.
• Mention any regional advantages or special services (e.g., fast delivery times, on-site consultation).
4. Contact Us Page:
• Clean and Simple Form: Include fields for general inquiries or specific product requests.
• Contact Information: Display the company’s, email address info@flo7k3.co.uk.
5. Additional Functionalities:
• Responsive Design: Ensure the design is fully responsive, optimised for mobile, tablet, and desktop viewing.
• SEO Optimisation: Include best practices for search engine optimization (SEO), including clean URLs, meta tags, and image alt text.
• Fast Loading Speed: Optimise images, scripts, and code for fast loading times to improve user experience.
• Social Media Integration: Provide links to social media profiles (if applicable) and potentially include a feed for recent updates.
• Optional Blog: Create a blog space for sharing industry news, product updates, or educational content to engage with visitors and improve SEO.
Style Guide:
1. Color Palette:
• Use colors consistent with the Flo7K3 logo: Red (#FF0000) and Yellow (#FFD700) as primary colors. Incorporate neutral colors (such as white, gray, or black) for balance and readability.
• Accent colors may be introduced for subtle highlights, but the focus should be on the bold, energetic color scheme of Flo7K3.
2. Typography:
• Primary Font for Headings: A bold, modern sans-serif font that complements the strong branding of Flo7K3.
• Secondary Font for Body Text: Clean, easy-to-read sans-serif or serif font for optimal readability across devices.
• Typography Emphasis: Use large, bold typography for headlines to match the boldness of the logo and brand identity.
3. Imagery:
• Use high-quality industrial and technical imagery that reflects the air and gas purification products Flo7K3 distributes.
• Incorporate imagery showing products in action, e.g., in industrial settings or installations.
• Avoid clutter; ensure images are used to enhance user understanding, not overwhelm.
4. Icons:
• Utilise modern, flat-style icons that align with the clean and professional image of Flo7K3. Icons could represent services such as “Fast Delivery,” “Expert Support,” and “High-Quality Products.”
Functionality Requirements:
1. Content Management System (CMS): Build the site using WordPress for easy content management, allowing Flo7K3 staff to update content, product information, and blog posts.
2. Quote Request Integration: Ensure the site has a functional and easy-to-access “Request a Quote” form that appears on every product and service page.
3. Customer Support Section: Optionally include a section for FAQs, product guides, or a knowledge base to support customers and prospects.
4. Security: Implement SSL encryption and ensure that other security best practices (e.g., spam prevention for forms) are followed.
5. Multilingual Support (Optional): Provide the option to support multiple languages, depending on the regional scope of Flo7K3’s distribution services.
Deliverables:
• WordPress template with a homepage, product pages, about section, and contact page.
• SEO-friendly and responsive design.
• Clear CTAs for lead generation (e.g., “Request a Quote”).
• User-friendly interface for both desktop and mobile devices.
Inspiration/Competitors:
• Competitor Analysis: Research similar distributors in the air and gas purification industry for design inspiration.
• Brand Consistency: Ensure Flo7K3’s bold branding is prominent and differentiates it from competitors.
Target Market(s)
Food & Beverage manufacturers, Laser Cutting, Electronics manufacturers, General Industrial Manufacturers

```html
<!DOCTYPE html>
<html lang="en">
<head>
<meta charset="utf-8">
<title>Flo7K3 – Nitrogen Generation Solutions</title>
<link href="https://fonts.googleapis.com/css2?family=Montserrat:wght@400;500;600;700&display=swap" rel="stylesheet">
<style>
:root{
  --red:#d0211c;
  --yellow:#fbbb00;
  --dark:#05080d;
  --navy:#0d1a2b;
  --grey-bg:#e9e9e9;
  --text:#555;
  --heading:#111;
  --white:#fff;
}
*{box-sizing:border-box;margin:0;padding:0}
html,body{width:1200px;height:5333px;overflow:hidden}
body{font-family:'Montserrat',sans-serif;color:var(--text);background:var(--white);position:relative}
.abs{position:absolute}
.btn{position:absolute;background:var(--red);color:var(--white);font-weight:600;font-size:15px;display:flex;align-items:center;justify-content:center;text-transform:uppercase;letter-spacing:.3px}
.section-title{position:absolute;left:0;width:1200px;text-align:center;font-size:34px;font-weight:600;color:var(--heading)}
.title-rule{position:absolute;left:570px;width:60px;height:4px;background:var(--yellow)}

/* header */
.site-header{position:absolute;top:0;left:0;width:1200px;height:83px;background:var(--white)}
.brand{position:absolute;left:100px;top:18px;font-size:40px;font-weight:700;color:var(--red);letter-spacing:-1px;display:flex;align-items:center;gap:10px}
.brand-dot{width:14px;height:14px;border-radius:50%;background:var(--yellow)}
.main-nav{position:absolute;left:348px;top:31px;display:flex;gap:30px;font-size:15px;font-weight:500;color:#222}
.main-nav .current{color:var(--red);position:relative;padding-left:18px}
.main-nav .current:before{content:"";position:absolute;left:0;top:6px;width:8px;height:8px;border-radius:50%;background:var(--red)}
.header-phone{position:absolute;left:912px;top:21px;display:flex;align-items:center;gap:10px;font-size:15px;font-weight:600;color:#111}
.phone-badge{width:40px;height:40px;border-radius:50%;background:var(--yellow);display:flex;align-items:center;justify-content:center}

/* hero */
.hero{position:absolute;top:83px;left:0;width:1200px;height:492px;background:linear-gradient(100deg,#e2301b 0%,#f0561d 40%,#f79a17 75%,#f5c21c 100%)}
.hero h1{position:absolute;top:152px;width:1200px;text-align:center;color:var(--white);font-size:56px;font-weight:500}
.hero p{position:absolute;top:237px;width:1200px;text-align:center;color:var(--white);font-size:15px;font-weight:600}
.hero-dots{position:absolute;top:361px;left:550px;display:flex;gap:8px}
.hero-dots span{width:14px;height:14px;border-radius:50%;background:var(--white)}
.hero-dots .on{background:transparent;border:3px solid var(--white)}

/* about */
.about{position:absolute;top:575px;left:0;width:1200px;height:656px;background:var(--dark)}
.about-frame{position:absolute;left:142px;top:138px;width:420px;height:400px;border:3px solid var(--white)}
.about-photo{position:absolute;left:175px;top:83px;width:388px;height:432px;background:linear-gradient(160deg,#4a4a3a,#2a3550 60%,#1b2233)}
.about-product{position:absolute;left:41px;top:205px;width:250px;height:365px;background:linear-gradient(90deg,#cfd3d6,#f4f5f6 50%,#b8bdc1)}
.about h2{position:absolute;left:623px;top:112px;color:var(--white);font-size:34px;font-weight:600}
.about .lead{position:absolute;left:623px;top:186px;width:475px;color:#d8d8d8;font-size:15px;line-height:30px}
.about .contact-line{position:absolute;left:623px;top:400px;color:#d8d8d8;font-size:15px}

/* product category */
.products{position:absolute;top:1231px;left:0;width:1200px;height:727px;background:var(--grey-bg)}
.cat-tabs{position:absolute;left:97px;top:179px;width:313px;height:258px;border-left:3px solid #333}
.cat-tab{position:absolute;left:0;width:313px;height:68px;padding-left:37px;display:flex;align-items:center;font-size:15px;font-weight:500;color:#222}
.cat-tab.active{background:var(--white);border-left:8px solid var(--yellow);margin-left:-3px;padding-left:32px}
.cat-card{position:absolute;left:428px;top:179px;width:671px;height:463px;background:var(--white)}
.cat-image{position:absolute;left:0;top:0;width:671px;height:285px;background:radial-gradient(circle at 60% 50%,#3da33d,#2a7a2a 40%,#173d17)}
.cat-card h3{position:absolute;left:29px;top:305px;font-size:25px;font-weight:500;color:#111}
.cat-card p{position:absolute;left:29px;top:350px;width:420px;font-size:14px;line-height:21px;color:#666}

/* why choose */
.why-card{position:absolute;top:2149px;width:244px;height:310px;background:var(--white);border:1px solid #e3e3e3;text-align:center;clip-path:polygon(0 0,100% 0,100% 88%,88% 100%,0 100%);z-index:2}
.why-card.dark{background:var(--navy);color:var(--white)}
.why-card svg{margin-top:24px}
.why-card h4{margin-top:18px;font-size:15px;font-weight:700;color:#111;line-height:24px;padding:0 10px}
.why-card.dark h4{color:var(--white)}
.why-card p{margin:14px auto 0;width:200px;font-size:12.5px;line-height:21px;color:#555}
.why-card.dark p{color:#e6e6e6}
.plant-band{position:absolute;top:2462px;left:0;width:1200px;height:370px;background:linear-gradient(180deg,#c8c6c3 0%,#a9a092 45%,#5b6a7e 80%,#35465c 100%)}

/* services */
.service-card{position:absolute;top:3028px;width:323px;height:421px;background:var(--white);border:1px solid #e3e3e3}
.service-image{position:absolute;left:17px;top:19px;width:289px;height:213px}
.service-card h4{position:absolute;left:25px;top:255px;font-size:21px;font-weight:500;color:#111}
.service-card p{position:absolute;left:25px;top:290px;width:275px;font-size:15px;line-height:25px;color:#666}

/* testimonials */
.testimonials{position:absolute;top:3555px;left:0;width:1200px;height:593px;background:var(--yellow)}
.testimonials h2{position:absolute;left:103px;top:150px;font-size:34px;font-weight:600;line-height:48px;color:#111}
.testimonials .red-rule{position:absolute;left:103px;top:252px;width:60px;height:4px;background:var(--red)}
.testimonials .intro{position:absolute;left:103px;top:290px;width:400px;font-size:14px;line-height:28px;color:#333}
.t-line{position:absolute;left:557px;top:71px;width:2px;height:456px;background:#fff}
.t-item{position:absolute;left:559px;width:346px;padding:14px 27px}
.t-item h5{font-size:25px;font-weight:500;color:#111}
.t-item p{margin-top:8px;font-size:14px;line-height:28px;color:#333}
.t-item.active{background:var(--red)}
.t-item.active h5,.t-item.active p{color:var(--white)}
.t-photo{position:absolute;left:906px;top:167px;width:233px;height:256px;background:var(--white);padding:10px}
.t-photo div{width:100%;height:100%;background:linear-gradient(135deg,#8fa8c4,#dfe6ee 50%,#3c5a80)}

/* contact */
.field{position:absolute;border:1px solid #cfcfcf;background:var(--white);font-size:16px;color:#444;padding:0 14px;display:flex;align-items:center}
.field.area{align-items:flex-start;padding-top:22px}

/* footer */
.site-footer{position:absolute;top:4883px;left:0;width:1200px;height:450px;background:#000}
.newsletter{position:absolute;left:110px;top:4792px;width:981px;height:211px;background:var(--white);box-shadow:0 2px 12px rgba(0,0,0,.15);z-index:3}
.newsletter h2{position:absolute;top:42px;width:981px;text-align:center;font-size:34px;font-weight:600;color:#111}
.newsletter .email{position:absolute;left:109px;top:101px;width:547px;height:67px;background:#e8e8e8;display:flex;align-items:center;padding-left:32px;font-size:16px;font-weight:500;color:#222}
.footer-brand{position:absolute;top:5040px;left:0;width:1200px;display:flex;justify-content:center;align-items:center;gap:12px;font-size:68px;font-weight:700;color:var(--red);letter-spacing:-1px}
.footer-nav{position:absolute;top:5175px;left:0;width:1200px;display:flex;justify-content:center;gap:46px;font-size:22px;font-weight:600;color:var(--white)}
.copyright{position:absolute;top:5258px;left:0;width:1200px;text-align:center;font-size:16px;font-weight:500;color:var(--white)}
</style>
</head>
<body>

<header class="site-header">
  <div class="brand"><span>Flo7K3</span><span class="brand-dot"></span></div>
  <nav class="main-nav">
    <span class="current">Home</span><span>About</span><span>Product</span><span>Services</span><span>Industries</span><span>Contact</span>
  </nav>
  <div class="header-phone">
    <span class="phone-badge"><svg width="18" height="18" viewBox="0 0 24 24"><path fill="#fff" d="M6.6 10.8a15 15 0 0 0 6.6 6.6l2.2-2.2c.3-.3.7-.4 1-.2 1.1.4 2.3.6 3.6.6.6 0 1 .4 1 1V20c0 .6-.4 1-1 1A17 17 0 0 1 3 4c0-.6.4-1 1-1h3.5c.6 0 1 .4 1 1 0 1.3.2 2.5.6 3.6.1.3 0 .7-.2 1z"/></svg></span>
    +1 555-010-0199
  </div>
</header>

<section class="hero" role="img" aria-label="Industrial pipework and refinery at sunset in red and yellow tones">
  <h1>Flo7K3 specialises</h1>
  <p>Flo7K3 specialises in supplying, installing, and servicing nitrogen generators.</p>
  <span class="btn" style="left:497px;top:283px;width:203px;height:48px">Request a quote</span>
  <div class="hero-dots"><span></span><span></span><span class="on"></span><span></span><span></span></div>
</section>

<section class="about">
  <div class="about-frame"></div>
  <div class="about-photo" role="img" aria-label="Engineer in hard hat checking a tablet beside industrial pipes"></div>
  <div class="about-product" role="img" aria-label="Two white nitrogen generator units"></div>
  <h2>ABOUT US</h2>
  <p class="lead">Flo7K3 specialises in supplying, installing, and servicing nitrogen generators for efficient on-site nitrogen production. Enhance your operations with our reliable, cost-effective nitrogen solutions. Discover how our advanced nitrogen generators can optimise your business today.</p>
  <p class="contact-line">Contact Flo7K3 for expert nitrogen generation services.</p>
  <span class="btn" style="left:627px;top:456px;width:176px;height:52px">Read more</span>
</section>

<section class="products">
  <h2 class="section-title" style="top:80px">PRODUCT CATEGORY</h2>
  <div class="title-rule" style="top:127px"></div>
  <div class="cat-tabs">
    <div class="cat-tab active" style="top:0">AIR FILTRATION SYSTEMS</div>
    <div class="cat-tab" style="top:78px">NITROGEN GENERATORS</div>
    <div class="cat-tab" style="top:142px">PRE-TREATMENT</div>
    <div class="cat-tab" style="top:210px">SENSORS</div>
  </div>
  <article class="cat-card">
    <div class="cat-image" role="img" aria-label="Glass globe on grass with green eco icons around it"></div>
    <h3>FLO7K3 AS A DISTRIBUTOR</h3>
    <p>Sed ut perspiciatis unde omnis iste natus error sit voluptatem accusantium doloremque laudantium, totam rem aperiam, eaque ipsa quae ab illo inventore veritatis et quasi architecto beatae</p>
    <span class="btn" style="left:482px;top:352px;width:177px;height:50px">Read more</span>
  </article>
</section>

<h2 class="section-title" style="top:2045px">WHY CHOOSE FLO7K3</h2>
<div class="title-rule" style="top:2094px"></div>

<div class="why-card" style="left:97px">
  <svg width="70" height="70" viewBox="0 0 70 70" fill="none" stroke="#e5531a" stroke-width="2.5"><path d="M20 12l10-4 10 4v10c0 8-5 13-10 15-5-2-10-7-10-15z"/><circle cx="48" cy="18" r="8"/><path d="M8 50l14-6h12l10 6-10 4H22M8 60h28l18-12"/><text x="26" y="44" font-size="14" fill="#e5531a" stroke="none">$</text></svg>
  <h4>MAJOR BENEFITS</h4>
  <p>"Lorem ipsum dolor sit amet, consectetur adipiscing elit, sed do eiusmod tempor incididunt ut labore et dolore magna aliqua</p>
</div>
<div class="why-card dark" style="left:352px">
  <svg width="70" height="70" viewBox="0 0 70 70" fill="none" stroke="#fff" stroke-width="2.5"><circle cx="40" cy="30" r="20"/><path d="M40 18v12l8 6M8 30h14M6 40h16M10 50h14M16 60l10-10"/></svg>
  <h4>QUICK DELIVERY</h4>
  <p>"Lorem ipsum dolor sit amet, consectetur adipiscing elit, sed do eiusmod tempor incididunt ut labore et dolore magna aliqua</p>
</div>
<div class="why-card" style="left:604px">
  <svg width="70" height="70" viewBox="0 0 70 70" fill="none" stroke="#e5531a" stroke-width="2.5"><circle cx="36" cy="46" r="7"/><path d="M24 64c0-8 6-12 12-12s12 4 12 12M10 14h14v10H10zM22 8h10M44 18h18v14H44zM24 20l8 14M44 28l-6 10"/></svg>
  <h4>EXPERT CONSULTATION</h4>
  <p>"Lorem ipsum dolor sit amet, consectetur adipiscing elit, sed do eiusmod tempor incididunt ut labore et dolore magna aliqua</p>
</div>
<div class="why-card" style="left:857px">
  <svg width="70" height="70" viewBox="0 0 70 70" fill="none" stroke="#e5531a" stroke-width="2.5"><circle cx="35" cy="32" r="16"/><circle cx="35" cy="32" r="6"/><path d="M29 50h12v8H29zM35 6v6M14 14l4 4M56 14l-4 4M8 32h6M56 32h6"/></svg>
  <h4>INNOVATIVE<br>TECHNOLOGY</h4>
  <p style="margin-top:8px">"Lorem ipsum dolor sit amet, consectetur adipiscing elit, sed do eiusmod tempor incididunt ut labore et dolore magna aliqua</p>
</div>
<div class="plant-band" role="img" aria-label="Refinery towers under a cloudy evening sky"></div>

<h2 class="section-title" style="top:2920px">OUR SERVICES</h2>
<div class="title-rule" style="top:2970px"></div>

<article class="service-card" style="left:97px">
  <div class="service-image" role="img" aria-label="Factory chimneys with smoke over a city" style="background:linear-gradient(180deg,#8a8078,#5a4a44 60%,#2d2a2c)"></div>
  <h4>CONSULTATION</h4>
  <p>Lorem ipsum dolor sit amet, consectetur adipiscing elit, sed do eiusmod tempor incididunt ut labore et dolore magna aliqua. Ut</p>
</article>
<article class="service-card" style="left:437px">
  <div class="service-image" role="img" aria-label="Hands fitting a pipe valve" style="background:linear-gradient(135deg,#d9d4cf,#b7aba2 50%,#8c7f76)"></div>
  <h4>INSTALLATION</h4>
  <p>Lorem ipsum dolor sit amet, consectetur adipiscing elit, sed do eiusmod tempor incididunt ut labore et dolore magna aliqua. Ut</p>
</article>
<article class="service-card" style="left:776px">
  <div class="service-image" role="img" aria-label="Pressure gauges on a gas regulator" style="background:linear-gradient(135deg,#6f9cc8,#cfdbe6 50%,#2f5b86)"></div>
  <h4>MAINTENANCE</h4>
  <p>Lorem ipsum dolor sit amet, consectetur adipiscing elit, sed do eiusmod tempor incididunt ut labore et dolore magna aliqua. Ut</p>
</article>

<section class="testimonials">
  <h2>TESTIMONIALS<br>/PARTNER</h2>
  <div class="red-rule"></div>
  <p class="intro">Sed ut perspiciatis unde omnis iste natus error sit voluptatem accusantium doloremque laudantium, totam rem aperiam, eaque ipsa</p>
  <div class="t-line"></div>
  <div class="t-item" style="top:72px"><h5>John Deo</h5><p>Sed ut perspiciatis unde omnis iste<br>natus error sit voluptatem</p></div>
  <div class="t-item active" style="top:233px"><h5>John Deo</h5><p>Sed ut perspiciatis unde omnis iste<br>natus error sit voluptatem</p></div>
  <div class="t-item" style="top:403px"><h5>John Deo</h5><p>Sed ut perspiciatis unde omnis iste<br>natus error sit voluptatem</p></div>
  <div class="t-photo"><div role="img" aria-label="Portrait of a client"></div></div>
</section>

<h2 class="section-title" style="top:4210px">CONTACT US</h2>
<div class="field" style="left:180px;top:4305px;width:418px;height:69px">First Name</div>
<div class="field" style="left:610px;top:4305px;width:418px;height:69px">Last Name</div>
<div class="field" style="left:180px;top:4384px;width:418px;height:70px">Email</div>
<div class="field" style="left:610px;top:4384px;width:418px;height:70px">Phone Number</div>
<div class="field area" style="left:180px;top:4473px;width:848px;height:139px">First Name</div>
<span class="btn" style="left:519px;top:4641px;width:162px;height:53px;font-size:12px">Read more</span>

<footer class="site-footer"></footer>
<div class="newsletter">
  <h2>OUR NEWSLETTER</h2>
  <div class="email">Enter &nbsp;Your Email</div>
  <span class="btn" style="left:674px;top:101px;width:193px;height:67px">Read more</span>
</div>
<div class="footer-brand"><span>Flo7K3</span><span class="brand-dot" style="width:22px;height:22px"></span></div>
<nav class="footer-nav"><span>Home</span><span>About</span><span>Product</span><span>Services</span><span>Industries</span><span>Blog</span><span>Contact</span></nav>
<p class="copyright">Copyright 2024 Flo7K3 All Rights Reserved</p>

</body>
</html>
```